Concierge Healthcare Business Card Design and Logo

We need a logo and business card design for a new company called "Sound Haven". We will provide concierge audiological care, hearing aids, hearing exams, custom hearing protection etc to patients in the comfort of their homes and offices. We would like a sleek and modern design preferably with an Ear related logo.

Target Market(s)

People with hearing loss, Hunters, Musicians
My usual clientele are older individuals so usually 50+ years old

Industry/Entity Type

Health Care

Contact Information for Business Card

Celia Brandt, AuD
Audiologist
512-648-2917
soundhaven@mailvoro.com
www.soundhaven-vorel.com

Logo Text

Sound Haven

Number of Pages Required

3 page

```html
<!DOCTYPE html>
<html lang="en">
<head>
<meta charset="utf-8">
<title>Sound Haven – Business Card</title>
<link rel="stylesheet" href="https://fonts.googleapis.com/css2?family=Open+Sans:wght@400;600;700&display=swap">
<style>
  :root {
    --stage: #e9e9e7;
    --card-white: #ffffff;
    --card-dark: #2a2a2c;
    --brand-blue: #1b8fd6;
    --brand-grey: #7b7c7e;
    --text-dark: #3a3a3c;
    --text-light: #ffffff;
  }
  * { box-sizing: border-box; margin: 0; padding: 0; }
  html, body {
    width: 1200px; height: 900px; overflow: hidden;
    background: var(--stage);
    font-family: "Open Sans", Arial, sans-serif;
  }
  .stage {
    position: relative; width: 1200px; height: 900px;
  }
  .card {
    position: absolute; left: 290px;
    width: 620px; height: 354px;
    box-shadow: 0 6px 18px rgba(0,0,0,.18);
    overflow: hidden;
  }
  .card--back { top: 60px; background: var(--card-dark); }
  .card--front { top: 486px; background: var(--card-white); }

  .wordmark {
    position: absolute; display: flex; align-items: center; gap: 14px;
    font-weight: 700; letter-spacing: 1.5px; white-space: nowrap;
  }
  .wordmark__dot { border-radius: 50%; flex: none; }
  .card--back .wordmark {
    left: 50%; top: 50%; transform: translate(-50%, -50%);
    color: var(--text-light); font-size: 40px;
  }
  .card--back .wordmark__dot { width: 30px; height: 30px; background: var(--text-light); }
  .card--front .wordmark {
    right: 44px; top: 150px;
    color: var(--brand-blue); font-size: 30px;
  }
  .card--front .wordmark__dot { width: 24px; height: 24px; background: var(--brand-blue); }

  .card__shapes { position: absolute; inset: 0; }

  .holder { position: absolute; left: 80px; top: 18px; }
  .holder__name { color: var(--brand-blue); font-weight: 700; font-size: 19px; line-height: 1.15; }
  .holder__role { color: var(--text-dark); font-size: 13px; }

  .contact {
    position: absolute; left: 34px; top: 168px;
    color: var(--text-dark); font-size: 14.5px; line-height: 1.45;
  }
  .contact__address { margin-bottom: 2px; padding-left: 26px; }
  .contact__line { display: flex; align-items: center; gap: 10px; }
  .contact__icon { width: 16px; height: 16px; flex: none; fill: var(--brand-blue); }
</style>
</head>
<body>
<main class="stage">

  <section class="card card--back" aria-label="Business card back">
    <div class="wordmark">
      <span class="wordmark__dot"></span>
      <span class="wordmark__name">SOUND HAVEN</span>
    </div>
  </section>

  <section class="card card--front" aria-label="Business card front">
    <svg class="card__shapes" width="620" height="354" viewBox="0 0 620 354" aria-hidden="true">
      <polygon points="0,0 40,0 22,28 0,28" fill="var(--brand-blue)"/>
      <polygon points="46,0 70,0 70,28 28,28" fill="var(--brand-grey)"/>
      <polygon points="0,306 276,306 262,326 0,326" fill="var(--brand-blue)"/>
      <polygon points="290,306 620,306 620,354 256,354" fill="var(--brand-grey)"/>
    </svg>

    <div class="holder">
      <p class="holder__name">Celia Brandt</p>
      <p class="holder__role">Managing Director</p>
    </div>

    <div class="contact">
      <p class="contact__address">4810 Vorel Lane, Suite 12<br>Austin, TX 78745.</p>
      <p class="contact__line">
        <svg class="contact__icon" viewBox="0 0 24 24" aria-hidden="true"><path d="M6.6 10.8a15.1 15.1 0 0 0 6.6 6.6l2.2-2.2a1 1 0 0 1 1-.25 11.4 11.4 0 0 0 3.6.57 1 1 0 0 1 1 1V20a1 1 0 0 1-1 1A17 17 0 0 1 3 4a1 1 0 0 1 1-1h3.5a1 1 0 0 1 1 1c0 1.25.2 2.45.57 3.57a1 1 0 0 1-.25 1z"/></svg>
        <span>512-648-2917</span>
      </p>
      <p class="contact__line">
        <svg class="contact__icon" viewBox="0 0 24 24" aria-hidden="true"><path d="M3 5h18v14H3z M3 5l9 7 9-7" fill="var(--brand-blue)" stroke="#fff" stroke-width="1.5"/></svg>
        <span>soundhaven@mailvoro.com</span>
      </p>
      <p class="contact__line">
        <svg class="contact__icon" viewBox="0 0 24 24" aria-hidden="true"><circle cx="12" cy="12" r="10"/><path d="M2 12h20M12 2c3 3 3 17 0 20M12 2c-3 3-3 17 0 20" fill="none" stroke="#fff" stroke-width="1.3"/></svg>
        <span>www.soundhaven-vorel.com</span>
      </p>
    </div>

    <div class="wordmark">
      <span class="wordmark__dot"></span>
      <span class="wordmark__name">SOUND HAVEN</span>
    </div>
  </section>

</main>
</body>
</html>
```